Fresh, modern, fun business card for pediatric dental practice

Need a business card for fresh, modern, fun pediatric dental practice

Clean look that matches our website's font and colors

We prefer the look of curved corners on business cards

Target Market(s)

parents (mothers) of young children, professionals, mid-high class

Industry/Entity Type

Dental

Contact Information for Business Card

Maplebrook Pediatric Dentistry
482 Quarry Lane
Suite 517
Fernwood, PA 17599
717.555.0193
www.maplebrookkidsdental.example

Mei-Ran Tsai, DMD
Corinne Walbeck, DMD
(we are working on our email address, but we would like that on the card as well)

Font styles to use
Sans Serif

Requirements
Must have
• All info; we would also like to make cards for individual staff members
• colors from our website and color palatte, attatched
• use same font and design as website for branding
Nice to have
• clean, simple card that has a pop of color
• we would like to see a few designs with our tag line "where smiles get brighter"
• we are not sure if we want to have it on there or not
• we would like to see a few designs incorporating the ribbon graphic on our website where the word WELCOME is

```html
<!DOCTYPE html>
<html lang="en">
<head>
<meta charset="utf-8">
<title>Maplebrook Pediatric Dentistry – Business Card</title>
<link rel="stylesheet" href="https://fonts.googleapis.com/css2?family=Open+Sans:wght@600&family=Roboto+Condensed:wght@500&family=Roboto:wght@400&display=swap">
<style>
  :root{
    --backdrop:#222222;
    --card-white:#f4f4f2;
    --sun-orange:#f0b024;
    --berry:#c92f8a;
    --ink:#4a4a4a;
    --paper-text:#ffffff;
  }
  *{margin:0;padding:0;box-sizing:border-box}
  html,body{width:1200px;height:960px;overflow:hidden;background:var(--backdrop)}
  .canvas{position:relative;width:1200px;height:960px}
  .card{position:absolute;width:600px;height:342px;border-radius:22px;overflow:hidden}
  .card-front{left:314px;top:113px;background:var(--card-white)}
  .card-back{left:311px;top:472px;background:var(--berry)}

  .doctors{position:absolute;right:40px;top:40px;text-align:right;
    font-family:"Roboto Condensed",sans-serif;font-weight:500;font-size:21px;line-height:25px;color:var(--sun-orange)}

  .brand{position:absolute;left:37px;top:92px;color:var(--sun-orange);
    font-family:"Open Sans",sans-serif;font-weight:600}
  .brand-dot{display:block;width:48px;height:48px;border-radius:50%;background:var(--sun-orange);margin:0 0 12px 88px}
  .brand-name{display:block;font-size:36px;line-height:38px;letter-spacing:.5px}
  .brand-sub{display:block;font-size:19px;line-height:24px;letter-spacing:.6px}

  .rule{position:absolute;left:37px;right:40px;top:228px;height:1px;background:var(--sun-orange)}

  .address{position:absolute;left:37px;top:239px;font-family:"Roboto",sans-serif;
    font-size:14.5px;line-height:18px;color:var(--ink);font-style:normal}
  .contact{position:absolute;right:40px;top:274px;list-style:none;text-align:right;
    font-family:"Roboto",sans-serif;font-size:14.5px;line-height:19px;color:var(--ink)}
  .contact li{display:flex;justify-content:flex-end;align-items:center;gap:5px}
  .contact svg{width:13px;height:13px;flex:none}

  .back-brand{position:absolute;right:40px;top:206px;display:flex;align-items:center;gap:10px;
    font-family:"Open Sans",sans-serif;font-weight:600;font-size:24px;color:var(--sun-orange)}
  .back-brand .brand-dot{width:34px;height:34px;margin:0}
  .back-url{position:absolute;right:50px;top:294px;font-family:"Roboto",sans-serif;font-size:14.5px;color:var(--paper-text)}
</style>
</head>
<body>
<main class="canvas">
  <section class="card card-front" aria-label="Card front">
    <p class="doctors">Mei-Ran Tsai, DMD<br>Corinne Walbeck, DMD</p>
    <div class="brand">
      <span class="brand-dot" aria-hidden="true"></span>
      <span class="brand-name">maplebrook</span>
      <span class="brand-sub">pediatric dentistry</span>
    </div>
    <div class="rule"></div>
    <address class="address">
      Maplebrook Pediatric Dentistry<br>
      482 Quarry Lane<br>
      Suite 517<br>
      Fernwood, PA 17599
    </address>
    <ul class="contact">
      <li>717.555.0193
        <svg viewBox="0 0 16 16" aria-hidden="true"><path fill="#f0b024" d="M3.6 1.2l2.3 2.6-1.2 1.8c.9 2 2.5 3.6 4.5 4.5l1.8-1.2 2.6 2.3-1.1 2.6C7 13.6 2.4 9 1 3.3z"/></svg>
      </li>
      <li>maplebrookkidsdental.example
        <svg viewBox="0 0 16 16" aria-hidden="true"><circle cx="8" cy="8" r="7" fill="#f0b024"/><path d="M1 8h14M8 1c-3 3.5-3 10.5 0 14M8 1c3 3.5 3 10.5 0 14" stroke="#f4f4f2" stroke-width="1.1" fill="none"/></svg>
      </li>
    </ul>
  </section>

  <section class="card card-back" aria-label="Card back">
    <div class="back-brand">
      <span class="brand-dot" aria-hidden="true"></span>
      <span>maplebrook</span>
    </div>
    <p class="back-url">www.maplebrookkidsdental.example</p>
  </section>
</main>
</body>
</html>
```